Finiding oppertunites in Real Estate 6.15.20

size of ad 7” x 9.6”
1-I like the ad to stand out and attract people's attention.
2-you should be able to see the text of the ad clearly .. see the attachment anything in yellow is instructions.
3-the list of topics should not be the main part of the ad
4-if you decide you want a picture or vector of a person .. (you decide)
then it should be a white male about 25-30 years old wearing a solid white or blue shirt and not long hair.
5-leave 1 inch for footer
see attachment
Good luck

Target Market(s)

potential male students 25-35 years of age

Industry/Entity Type

Education

Requirements
Must have
• will stand out and people would want to see it.
should be able to read the words of ad
Nice to have
• how to make money in real estate on one line

```html
<!DOCTYPE html>
<html lang="en">
<head>
<meta charset="utf-8">
<title>Real Estate Career Course</title>
<link rel="stylesheet" href="https://fonts.googleapis.com/css2?family=Catamaran:wght@600;700;800;900&family=League+Spartan:wght@700;800&family=Questrial&family=Open+Sans:ital,wght@1,800&display=swap">
<style>
  :root{
    --gold:#B99A5B;
    --gold-deep:#C2A157;
    --gold-light:#E3D0A2;
    --navy:#284672;
    --red:#E3202A;
    --ink:#222;
    --cream:#EFE5CE;
    --white:#fff;
  }
  *{margin:0;padding:0;box-sizing:border-box}
  html,body{width:875px;height:1200px;overflow:hidden;background:var(--white)}
  .ad{position:relative;width:875px;height:1200px;background:var(--white);overflow:hidden;font-family:"Catamaran",sans-serif}
  .title{position:absolute;left:0;width:100%;text-align:center;font-family:"League Spartan",sans-serif;font-weight:800;color:var(--gold);line-height:1}
  .title--one{top:47px;font-size:68px}
  .title--two{top:110px;font-size:71px}
  .banner{position:absolute;left:128px;width:620px;background:var(--navy);color:var(--white);text-align:center;font-weight:700;box-shadow:3px 5px 8px rgba(0,0,0,.28);border:1px solid #fff;white-space:nowrap}
  .banner--question{top:196px;height:49px;font-size:37px;line-height:52px}
  .banner--audience{top:271px;height:76px;font-size:38px;line-height:34px;padding-top:6px}
  .slogan{position:absolute;top:379px;left:0;width:100%;text-align:center;color:var(--red);font-weight:900;font-size:46.5px;line-height:45px;white-space:nowrap}
  .houses{position:absolute;top:500px;left:0;width:875px;height:140px}
  .promo{position:absolute;left:86px;top:678px;width:704px;height:199px;background:linear-gradient(90deg,var(--gold-deep) 0%,var(--gold-light) 50%,var(--gold-deep) 100%)}
  .promo__art{position:absolute;left:50px;top:16px;width:215px;height:122px}
  .promo__remote{position:absolute;left:52px;top:96px;font-family:"Questrial",sans-serif;color:var(--white);font-size:50px;line-height:42px}
  .promo__divider{position:absolute;left:351px;top:11px;width:2px;height:177px;background:var(--white)}
  .promo__sessions{position:absolute;left:373px;width:310px;top:14px;text-align:center;font-family:"Questrial",sans-serif;color:var(--white);font-size:50px;line-height:38px}
  .promo__start{position:absolute;left:373px;top:103px;width:313px;height:81px;background:var(--white);text-align:center;color:var(--navy)}
  .promo__start-label{display:block;font-family:"Questrial",sans-serif;font-size:40px;line-height:40px;margin-top:3px}
  .promo__start-date{display:block;font-family:"League Spartan",sans-serif;font-weight:800;font-size:43px;line-height:36px}
  .topics-bg{position:absolute;top:915px;left:0;width:875px;height:160px;background:linear-gradient(180deg,var(--white) 0%,var(--cream) 100%)}
  .topics-title{position:absolute;top:896px;left:0;width:100%;text-align:center;color:var(--navy);font-weight:700;font-size:25px}
  .topics{position:absolute;top:934px;list-style:none}
  .topics li{position:relative;height:26.8px;padding-left:28px;font-family:"Questrial",sans-serif;font-size:15.5px;color:var(--ink);line-height:22px;white-space:nowrap}
  .topics svg{position:absolute;left:0;top:5px}
  .topics--a{left:110px}.topics--b{left:367px}.topics--c{left:621px}
  .contact{position:absolute;font-family:"Questrial",sans-serif;font-size:15.8px;color:var(--ink);white-space:nowrap}
  .contact--address{left:91px;top:1118px;line-height:19px;font-style:normal}
  .contact--lines{left:348px;top:1098px;line-height:24px}
  .contact--lines div{position:relative;padding-left:32px}
  .contact svg{position:absolute;left:0;top:5px}
  .pin{position:absolute;left:55px;top:1116px}
  .hotline{position:absolute;right:50px;top:1108px;text-align:right}
  .hotline__label{display:block;font-family:"League Spartan",sans-serif;font-weight:800;color:var(--red);font-size:37px;line-height:34px}
  .hotline__number{display:block;font-family:"Open Sans",sans-serif;font-style:italic;font-weight:800;font-size:18px;color:var(--ink)}
</style>
</head>
<body>
<main class="ad">
  <h1 class="title title--one">REAL ESTATE</h1>
  <h1 class="title title--two">CAREER COURSE</h1>

  <div class="banner banner--question">How to Make Money In Real Estate?</div>
  <div class="banner banner--audience">For those who have started or<br>would like to go into Real Estate.</div>

  <p class="slogan">An investment in knowledge<br>opens up untold opportunities.</p>

  <svg class="houses" role="img" aria-label="Rows of small white model houses with one red house in front" viewBox="0 0 875 140">
    <defs>
      <linearGradient id="houses-fade" x1="0" y1="0" x2="0" y2="1">
        <stop offset="0" stop-color="#fff"/>
        <stop offset=".5" stop-color="#e6e6e6"/>
        <stop offset="1" stop-color="#fff"/>
      </linearGradient>
    </defs>
    <rect width="875" height="140" fill="url(#houses-fade)"/>
    <rect x="390" y="78" width="75" height="55" fill="#d62a2a"/>
  </svg>

  <section class="promo">
    <svg class="promo__art" role="img" aria-label="Illustration of a man on a laptop attending an online real estate class" viewBox="0 0 215 122">
      <rect width="215" height="122" rx="6" fill="#d8c28c"/>
      <rect x="92" y="4" width="112" height="64" fill="#f0a048"/>
    </svg>
    <div class="promo__remote">REMOTE<br>SESSIONS</div>
    <div class="promo__divider"></div>
    <div class="promo__sessions">12 session<br>course</div>
    <div class="promo__start">
      <span class="promo__start-label">Classes starting</span>
      <span class="promo__start-date">June 16</span>
    </div>
  </section>

  <div class="topics-bg"></div>
  <h2 class="topics-title">A partial listing of Topics</h2>

  <svg width="0" height="0" style="position:absolute">
    <symbol id="tick" viewBox="0 0 14 14">
      <path d="M11 6.5V12.5H1.5V3H8" fill="none" stroke="#C2A157" stroke-width="1.2"/>
      <path d="M4 6.5l2.5 2.5L13 2" fill="none" stroke="#C2A157" stroke-width="1.3"/>
    </symbol>
  </svg>

  <ul class="topics topics--a">
    <li><svg width="14" height="14"><use href="#tick"/></svg>Single-family</li>
    <li><svg width="14" height="14"><use href="#tick"/></svg>Multifamily</li>
    <li><svg width="14" height="14"><use href="#tick"/></svg>Management</li>
    <li><svg width="14" height="14"><use href="#tick"/></svg>Real Estate Concepts</li>
    <li><svg width="14" height="14"><use href="#tick"/></svg>Real Estate law</li>
  </ul>
  <ul class="topics topics--b">
    <li><svg width="14" height="14"><use href="#tick"/></svg>Investment properties</li>
    <li><svg width="14" height="14"><use href="#tick"/></svg>Foreclosures</li>
    <li><svg width="14" height="14"><use href="#tick"/></svg>Rehab</li>
    <li><svg width="14" height="14"><use href="#tick"/></svg>Foreclosures</li>
    <li><svg width="14" height="14"><use href="#tick"/></svg>Short sales</li>
  </ul>
  <ul class="topics topics--c">
    <li><svg width="14" height="14"><use href="#tick"/></svg>Development</li>
    <li><svg width="14" height="14"><use href="#tick"/></svg>Finical modeling</li>
    <li><svg width="14" height="14"><use href="#tick"/></svg>HUD properties</li>
    <li><svg width="14" height="14"><use href="#tick"/></svg>Due Diligence</li>
  </ul>

  <svg class="pin" width="22" height="38" viewBox="0 0 22 38" aria-hidden="true">
    <path d="M11 1C5.5 1 1 5.3 1 10.8 1 18 11 30 11 30S21 18 21 10.8C21 5.3 16.5 1 11 1Z" fill="#C2A157"/>
    <path d="M6 12l5-4.5 5 4.5v4.5H6Z" fill="#fff"/>
    <ellipse cx="11" cy="34" rx="8" ry="2.5" fill="none" stroke="#C2A157" stroke-width="1.5"/>
  </svg>
  <address class="contact contact--address">48 Alder Park Avenue,<br>Suite 210 Westbrook</address>

  <div class="contact contact--lines">
    <div><svg width="16" height="16" viewBox="0 0 16 16"><path d="M3 1l3 3-1.5 2.5c1 2 3 4 5 5L12 10l3 3-2 2C7 15 1 9 1 3Z" fill="#C2A157"/></svg>+014 - 5827 - 30619</div>
    <div><svg width="18" height="13" viewBox="0 0 18 13"><rect width="18" height="13" fill="#C2A157"/><path d="M0 0l9 7 9-7" fill="none" stroke="#fff" stroke-width="1.3"/></svg>learn@keycourse.com</div>
    <div><svg width="16" height="16" viewBox="0 0 16 16"><circle cx="8" cy="8" r="7" fill="none" stroke="#C2A157" stroke-width="1.6"/><path d="M4 4c2 1 2 3 4 3s1 3 0 4M11 3c-1 2 1 3 2 3" fill="none" stroke="#C2A157" stroke-width="1.6"/></svg>keycourseonline.com</div>
  </div>

  <div class="hotline">
    <span class="hotline__label">HOTLINE</span>
    <span class="hotline__number">+014 - 5827 - 30619</span>
  </div>
</main>
</body>
</html>
```